Frostvale Harborline LLC

we need a business card design

Industry/Entity Type

hvac

Contact Information for Business Card

my logo

Requirements
Must have
• my logo and same colors

```html
<!DOCTYPE html>
<html lang="en">
<head>
<meta charset="utf-8">
<title>Frostvale Harborline LLC — Business Card</title>
<link href="https://fonts.googleapis.com/css2?family=Poppins:wght@300;400;700&display=swap" rel="stylesheet">
<style>
  :root {
    --stage: #979797;
    --brand-blue: #0060a7;
    --paper: #ffffff;
    --ink-grey: #4a4a4a;
  }
  * { margin: 0; padding: 0; box-sizing: border-box; }
  html, body {
    width: 1200px; height: 1000px; overflow: hidden;
    background: var(--stage);
    font-family: "Poppins", sans-serif;
  }
  .card {
    position: absolute;
    left: 241px;
    width: 719px;
    height: 414px;
  }
  .card-front { top: 70px; background: var(--brand-blue); color: var(--paper); }
  .card-back { top: 522px; background: var(--paper); color: var(--ink-grey); }

  .brand-name {
    position: absolute;
    left: 0; right: 0;
    display: flex;
    flex-direction: column;
    align-items: center;
    justify-content: center;
    text-align: center;
    font-weight: 700;
    line-height: 1.08;
  }
  .brand-name span { display: block; }
  .card-front .brand-name {
    top: 66px; height: 278px;
    font-size: 60px; color: var(--paper);
  }
  .card-back .brand-name {
    top: 51px; height: 171px;
    font-size: 37px; color: var(--brand-blue);
  }

  .front-url {
    position: absolute;
    top: 365px; left: 0; right: 0;
    text-align: center;
    font-weight: 700;
    font-size: 18px;
  }

  .contact {
    position: absolute;
    top: 242px; left: 0; right: 0;
    text-align: center;
    font-weight: 300;
    font-size: 18px;
    line-height: 23.5px;
  }
  .contact .location { margin-bottom: 14px; }
  .contact-icons {
    display: flex; justify-content: center; gap: 3px;
    margin-bottom: 8px;
  }
  .contact-icons svg { width: 22px; height: 22px; display: block; }
</style>
</head>
<body>
  <section class="card card-front">
    <h1 class="brand-name"><span>Frostvale</span><span>Harborline LLC</span></h1>
    <p class="front-url">frostvaleharborline.com</p>
  </section>

  <section class="card card-back">
    <h2 class="brand-name"><span>Frostvale</span><span>Harborline LLC</span></h2>
    <div class="contact">
      <p class="location">Harbor Point, FL, USA</p>
      <div class="contact-icons">
        <svg viewBox="0 0 22 22" aria-label="phone"><circle cx="11" cy="11" r="11" fill="#0060a7"/><path d="M7.5 6.5c.8-.6 1.4-.4 1.8.3l.8 1.5c.3.6.1 1-.4 1.4l-.5.4c.5 1.2 1.4 2.1 2.6 2.6l.4-.5c.4-.5.8-.7 1.4-.4l1.5.8c.7.4.9 1 .3 1.8-.8 1-2 1.3-3.4.6-2.300-1.1-4-2.8-5.1-5.1-.7-1.4-.4-2.6.6-3.4z" fill="#fff"/></svg>
        <svg viewBox="0 0 22 22" aria-label="email"><circle cx="11" cy="11" r="11" fill="#0060a7"/><rect x="5.5" y="7.5" width="11" height="7.5" fill="none" stroke="#fff" stroke-width="1.2"/><path d="M5.5 7.5 11 11.8 16.5 7.5M5.5 15 9.3 10.5M16.5 15 12.7 10.5" fill="none" stroke="#fff" stroke-width="1.1"/></svg>
        <svg viewBox="0 0 22 22" aria-label="website"><circle cx="11" cy="11" r="11" fill="#0060a7"/><g fill="none" stroke="#fff" stroke-width="1"><circle cx="11" cy="11" r="6"/><ellipse cx="11" cy="11" rx="2.6" ry="6"/><path d="M5 11h12M6 8h10M6 14h10M11 5v12"/></g></svg>
      </div>
      <p>727-555-0148</p>
      <p>dana@northgateairco.com</p>
      <p>frostvaleharborline.com</p>
    </div>
  </section>
</body>
</html>
```